Revamp Of Landing Page For an Automated AI Voice Agents Agency

here is my current landing page https://app.brightfernpromotionhub.biz/v2/preview/WXKRPmQ4hLzYBvNdTeGS?notrack=true

Please use all my current content and imagery of ai agents in your new design. Make it easy to ready, easy to navigate and easy to understand

I am looking for a SLEEK shiny polished looking website. I like Dark themed sites but am open to see light themed sites too so please dont be shy.

The site should have an Ai Voice Agent Theme about it. Maybe look and feel of futureistic but simple and not intimidating to the average person...

Here are a couple website designs I like for reference:
https://q7v.io/
https://ai-bots.marekholvin.com/
https://chatwelmo.com/ai-agents

Target Market(s)

b2b

Industry/Entity Type

AI Voice Agents

Coding

Coded - Design and coding required

Font styles to use
Other font styles liked:
• open

Requirements
Must have
• all elements and content and images used in existing design.
Nice to have
• open
Should not have
• open

```html
<!DOCTYPE html>
<html lang="en">
<head>
<meta charset="utf-8">
<title>Vocalynx – AI Voice Agents</title>
<link href="https://fonts.googleapis.com/css2?family=Manrope:wght@400;500;600;700;800&display=swap" rel="stylesheet">
<style>
:root{
  --board:#261d44;
  --page:#0f0f15;
  --hero-top:#17122e;
  --ink:#ffffff;
  --muted:#b7b3c9;
  --dim:#8a869c;
  --faint:#6e6a80;
  --violet:#9b4dff;
  --violet-soft:#a77bff;
  --blue:#3f7bff;
  --card:#23232a;
  --card-line:#34343d;
  --chat:#130f2e;
  --chat-line:#4b36c9;
}
*{margin:0;padding:0;box-sizing:border-box}
html,body{width:1200px;height:1200px;overflow:hidden}
body{background:var(--board);font-family:"Manrope",sans-serif;color:var(--ink);position:relative}

.frame{position:absolute;overflow:hidden;background:var(--page)}
.frame--desktop{left:45px;top:146px;width:723px;height:1054px}
.frame--overview{left:799px;top:146px;width:349px;height:908px}
.frame--overview .page{transform:scale(0.482);transform-origin:0 0}

.page{position:absolute;left:0;top:0;width:723px;background:var(--page)}
.frame--desktop .page{height:1054px}
.frame--overview .page{height:1884px}
.abs{position:absolute}
.center{left:0;right:0;text-align:center}

.hero-bg{position:absolute;left:0;top:0;width:723px;height:760px;
  background:
   radial-gradient(ellipse 260px 120px at 361px 265px,rgba(110,60,230,.55),transparent 70%),
   radial-gradient(ellipse 420px 200px at 300px 230px,rgba(70,40,170,.35),transparent 75%),
   linear-gradient(180deg,var(--hero-top) 0%,#141027 45%,var(--page) 100%)}

/* nav */
.brand{font-weight:700;letter-spacing:.06em;font-size:13px;display:flex;align-items:center;gap:6px}
.brand-dot{width:12px;height:12px;border-radius:50%;border:1.5px solid var(--ink)}
.nav-links{display:flex;gap:20px;font-size:8.5px;color:#e6e3f2;top:17px;left:268px}
.btn{display:flex;align-items:center;justify-content:center;border-radius:4px;font-weight:600;color:#fff;
  background:linear-gradient(90deg,var(--blue),var(--violet))}
.btn--nav{left:601px;top:12px;width:57px;height:20px;font-size:7.5px}

/* hero */
.hero-title{top:92px;font-size:32px;line-height:33px;font-weight:700;letter-spacing:-.02em}
.hero-title em{font-style:normal;color:var(--violet)}
.hero-sub{top:171px;font-size:8.4px;line-height:11.5px;color:#d4d0e2}
.btn--hero{left:311px;top:208px;width:101px;height:24px;font-size:8.5px;font-weight:500}
.hero-note{top:248px;font-size:5.3px;line-height:8.5px;color:#c8c3da}

.chat{left:132px;top:294px;width:460px;height:165px;border:1px solid var(--chat-line);border-radius:7px;
  background:linear-gradient(180deg,#1a1140,var(--chat));box-shadow:0 0 24px rgba(90,60,230,.35)}
.chat-avatar{left:15px;top:23px;width:21px;height:21px;border-radius:50%;background:linear-gradient(135deg,var(--blue),var(--violet));display:flex;align-items:center;justify-content:center}
.chat-bubble{left:42px;top:19px;width:402px;height:28px;border-radius:4px;background:#2a2547;border:1px solid #3a3460;font-size:8.3px;color:#ece9f6;display:flex;align-items:center;justify-content:center}
.mic{left:215px;top:67px;width:29px;height:29px;border-radius:50%;background:linear-gradient(135deg,var(--blue),var(--violet));display:flex;align-items:center;justify-content:center}
.chat-hint{top:137px;font-size:7.3px;color:var(--dim);letter-spacing:.02em}

.trust{top:492px;font-size:7.8px;color:#c3bfd1}
.partners{top:522px;left:186px;display:flex;gap:26px;font-size:14px;font-weight:600;color:#7a7788;align-items:center}
.partners span{display:flex;align-items:center;gap:4px}
.partners i{display:inline-block;width:9px;height:9px;background:#7a7788;border-radius:2px}

/* sections */
.sec-title{font-size:20px;font-weight:700}
.sec-sub{font-size:8.3px;color:var(--muted)}
.features-title{top:660px}
.features-sub{top:691px}

.feature{width:192px;height:101px;background:linear-gradient(180deg,#26262d,#1e1e24);border:1px solid var(--card-line);border-radius:4px;text-align:center}
.feature .ico{position:absolute;left:86px;top:15px;width:20px;height:20px;border-radius:50%;background:#33334a;display:flex;align-items:center;justify-content:center}
.feature h3{position:absolute;left:0;right:0;top:46px;font-size:10.2px;font-weight:500}
.feature p{position:absolute;left:18px;right:18px;top:67px;font-size:7.2px;line-height:9.6px;color:var(--muted)}

/* how it works */
.hiw-title{top:1066px}
.hiw-sub{top:1094px;font-size:7px}
.steps{left:64px;top:1137px;width:297px;height:170px;background:#25252c;border:1px solid var(--card-line);border-radius:4px;padding:12px 12px}
.step{display:flex;gap:8px;margin-bottom:10px}
.step-num{flex:none;width:13px;height:13px;border-radius:50%;background:var(--violet-soft);font-size:6px;display:flex;align-items:center;justify-content:center}
.step h4{font-size:8.6px;font-weight:500;margin-bottom:3px}
.step p{font-size:6.4px;line-height:9px;color:var(--muted)}
.orbit{left:434px;top:1139px;width:166px;height:166px;border-radius:50%;
  background:radial-gradient(circle,#1c1740 0%,#15122b 60%,#121020 100%);box-shadow:0 0 30px rgba(90,60,220,.3)}
.orbit-ring{position:absolute;inset:18px;border-radius:50%;border:1px solid #2e2a55}
.orbit-node{position:absolute;width:32px;height:32px;border-radius:6px;background:#2d2a55;border:1px solid #4a44a0}

/* pricing */
.pricing-bg{left:0;top:1369px;width:723px;height:310px;background:#13131a}
.pricing-title{top:1405px}
.pricing-sub{top:1436px;font-size:7px}
.plan{top:1475px;width:183px;height:162px;background:#25252c;border:1px solid #3a3a44;border-radius:4px;padding:12px 12px}
.plan--popular{border-color:#6a5ad0}
.plan-badge{position:absolute;left:72px;top:-4px;width:36px;height:10px;border-radius:2px;background:var(--violet-soft);font-size:5px;display:flex;align-items:center;justify-content:center}
.plan-tier{font-size:7px;color:var(--muted)}
.plan-price{font-size:13px;font-weight:700;margin:3px 0 10px}
.plan-price small{font-size:5px;font-weight:400}
.plan li{list-style:none;font-size:6.2px;color:#cfcbe0;margin-bottom:7px;display:flex;gap:5px;align-items:center}
.plan li::before{content:"";width:5px;height:5px;background:var(--violet-soft);clip-path:polygon(50% 0,62% 38%,100% 50%,62% 62%,50% 100%,38% 62%,0 50%,38% 38%)}
.plan-btn{position:absolute;left:11px;right:11px;bottom:11px;height:17px;border-radius:3px;background:#0c0c10;font-size:6px;display:flex;align-items:center;justify-content:center}
.plan-btn--primary{background:linear-gradient(90deg,var(--blue),var(--violet))}

/* footer */
.footer-line{left:0;top:1680px;width:723px;height:1px;background:#24242c}
.footer-brand{left:124px;top:1740px}
.footer-brand .brand{font-size:12px}
.footer-tag{left:124px;top:1764px;font-size:6.5px;line-height:9px;color:var(--dim)}
.footer-col{top:1716px;font-size:6.5px;color:var(--dim)}
.footer-col h5{font-size:7px;color:#fff;font-weight:600;margin-bottom:10px}
.footer-col div{margin-bottom:9px}
.footer-bottom{left:104px;right:104px;top:1845px;border-top:1px solid #24242c}
.copyright{left:104px;top:1859px;font-size:6px;color:var(--faint)}
.social{top:1858px;left:1000px}
.social-dots{right:104px;top:1858px;display:flex;gap:10px}
.social-dots span{width:8px;height:8px;border-radius:50%;background:#8a869c}
</style>
</head>
<body>

<!-- Desktop view -->
<div class="frame frame--desktop">
  <div class="page">
    <div class="hero-bg"></div>

    <div class="abs brand" style="left:66px;top:14px"><span class="brand-dot"></span>VOCALYNX</div>
    <nav class="abs nav-links"><span>About</span><span>Features</span><span>Pricing</span><span>Integration</span><span>Contact</span></nav>
    <a class="abs btn btn--nav">Try Demo</a>

    <h1 class="abs center hero-title">Smarter Calls, Messages &amp;<br>Scheduling <em>Powered by AI</em></h1>
    <p class="abs center hero-sub">Experience seamless voice interactions powered by cutting-edge artificial intelligence.<br>Say hello to the future of communication.</p>
    <a class="abs btn btn--hero">Get An Free Demo</a>
    <p class="abs center hero-note">*14-Day Money Back Guarantee Terms: If you use the ai agents and you're not happy.<br>Then you can contact us in the first 14 days for a full refund.</p>

    <div class="abs chat">
      <div class="abs chat-avatar"><svg width="10" height="10" viewBox="0 0 10 10" fill="none" stroke="#fff" stroke-width="1"><rect x="2" y="3.5" width="6" height="4.5" rx="1"/><path d="M5 1.5v2"/><circle cx="4" cy="5.7" r=".4" fill="#fff"/><circle cx="6" cy="5.7" r=".4" fill="#fff"/></svg></div>
      <div class="abs chat-bubble">Hello, I'm Vocalynx, your voice AI assistant. How can I help you today?</div>
      <div class="abs mic"><svg width="12" height="12" viewBox="0 0 12 12" fill="none" stroke="#fff" stroke-width="1.1"><rect x="4.2" y="1" width="3.6" height="6" rx="1.8"/><path d="M2.5 5.5a3.5 3.5 0 0 0 7 0M6 9v2"/></svg></div>
      <svg class="abs" style="left:222px;top:104px" width="14" height="10" viewBox="0 0 14 10" fill="#8f7bff"><rect x="0" y="5" width="1.6" height="5"/><rect x="4" y="2" width="1.6" height="8"/><rect x="8" y="0" width="1.6" height="10"/><rect x="12" y="4" width="1.6" height="6"/></svg>
      <p class="abs center chat-hint">Click the microphone to start speaking</p>
    </div>

    <p class="abs center trust">The world's most popular workflow automation platform for technical teams including</p>
    <div class="abs partners"><span><i></i>Quillo</span><span>Meetra</span><span>Rydeo</span><span><i></i>Korvane</span><span><i></i>Tablix</span></div>

    <h2 class="abs center sec-title features-title">Features</h2>
    <p class="abs center sec-sub features-sub">Discover what makes our voice AI exceptional</p>

    <div class="abs feature" style="left:65px;top:731px"><span class="ico"><svg width="11" height="11" viewBox="0 0 12 12" fill="none" stroke="#b49bff" stroke-width="1"><circle cx="6" cy="6" r="4.5"/><path d="M6 1.5v9M3 4.5h6M3 7.5h6"/></svg></span><h3>Advanced AI</h3><p>Powered by state-of-the-art machine learning models for natural conversations.</p></div>
    <div class="abs feature" style="left:266px;top:731px;height:104px"><span class="ico"><svg width="11" height="11" viewBox="0 0 12 12" fill="none" stroke="#b49bff" stroke-width="1"><path d="M2 8V6a4 4 0 0 1 8 0v2"/><rect x="1.5" y="7" width="2" height="3" rx=".8"/><rect x="8.5" y="7" width="2" height="3" rx=".8"/></svg></span><h3>Clear Voice Recognition</h3><p style="top:70px">Industry-leading voice recognition that works even in noisy environments.</p></div>
    <div class="abs feature" style="left:467px;top:731px;height:104px"><span class="ico"><svg width="11" height="11" viewBox="0 0 12 12" stroke="#b49bff" stroke-width="1"><path d="M1 5v2M3 3v6M5 1v10M7 3v6M9 4v4M11 5v2"/></svg></span><h3>Natural Speech</h3><p style="top:70px">Generates human-like responses with appropriate tone and context.</p></div>
    <div class="abs feature" style="left:65px;top:845px"><span class="ico"><svg width="11" height="11" viewBox="0 0 12 12" fill="none" stroke="#b49bff" stroke-width="1"><path d="M7 1 2.5 7H6l-1 4 4.5-6H6z"/></svg></span><h3>Lightning Fast</h3><p>Get responses in milliseconds, with no perceivable delay.</p></div>
    <div class="abs feature" style="left:266px;top:845px"><span class="ico"><svg width="11" height="11" viewBox="0 0 12 12" fill="none" stroke="#b49bff" stroke-width="1"><path d="M6 1 2 2.5V6c0 2.5 1.8 4 4 5 2.2-1 4-2.5 4-5V2.5z"/></svg></span><h3>Private &amp; Secure</h3><p>Your conversations are encrypted and never stored without permission.</p></div>
    <div class="abs feature" style="left:467px;top:845px"><span class="ico"><svg width="11" height="11" viewBox="0 0 12 12" fill="none" stroke="#b49bff" stroke-width="1"><circle cx="6" cy="6" r="4.5"/><path d="M1.5 6h9M6 1.5c-2.4 2.5-2.4 6.5 0 9M6 1.5c2.4 2.5 2.4 6.5 0 9"/></svg></span><h3>Multilingual Support</h3><p>Communicate in over 30 languages with accurate translations.</p></div>
  </div>
</div>

<!-- Full page overview -->
<div class="frame frame--overview">
  <div class="page">
    <div class="hero-bg"></div>

    <div class="abs brand" style="left:66px;top:14px"><span class="brand-dot"></span>VOCALYNX</div>
    <nav class="abs nav-links"><span>About</span><span>Features</span><span>Pricing</span><span>Integration</span><span>Contact</span></nav>
    <a class="abs btn btn--nav">Try Demo</a>

    <h1 class="abs center hero-title">Smarter Calls, Messages &amp;<br>Scheduling <em>Powered by AI</em></h1>
    <p class="abs center hero-sub">Experience seamless voice interactions powered by cutting-edge artificial intelligence.<br>Say hello to the future of communication.</p>
    <a class="abs btn btn--hero">Get An Free Demo</a>
    <p class="abs center hero-note">*14-Day Money Back Guarantee Terms: If you use the ai agents and you're not happy.<br>Then you can contact us in the first 14 days for a full refund.</p>

    <div class="abs chat">
      <div class="abs chat-avatar"><svg width="10" height="10" viewBox="0 0 10 10" fill="none" stroke="#fff" stroke-width="1"><rect x="2" y="3.5" width="6" height="4.5" rx="1"/><path d="M5 1.5v2"/></svg></div>
      <div class="abs chat-bubble">Hello, I'm Vocalynx, your voice AI assistant. How can I help you today?</div>
      <div class="abs mic"><svg width="12" height="12" viewBox="0 0 12 12" fill="none" stroke="#fff" stroke-width="1.1"><rect x="4.2" y="1" width="3.6" height="6" rx="1.8"/><path d="M2.5 5.5a3.5 3.5 0 0 0 7 0M6 9v2"/></svg></div>
      <svg class="abs" style="left:222px;top:104px" width="14" height="10" viewBox="0 0 14 10" fill="#8f7bff"><rect x="0" y="5" width="1.6" height="5"/><rect x="4" y="2" width="1.6" height="8"/><rect x="8" y="0" width="1.6" height="10"/><rect x="12" y="4" width="1.6" height="6"/></svg>
      <p class="abs center chat-hint">Click the microphone to start speaking</p>
    </div>

    <p class="abs center trust">The world's most popular workflow automation platform for technical teams including</p>
    <div class="abs partners"><span><i></i>Quillo</span><span>Meetra</span><span>Rydeo</span><span><i></i>Korvane</span><span><i></i>Tablix</span></div>

    <h2 class="abs center sec-title features-title">Features</h2>
    <p class="abs center sec-sub features-sub">Discover what makes our voice AI exceptional</p>

    <div class="abs feature" style="left:65px;top:731px"><span class="ico"></span><h3>Advanced AI</h3><p>Powered by state-of-the-art machine learning models for natural conversations.</p></div>
    <div class="abs feature" style="left:266px;top:731px"><span class="ico"></span><h3>Clear Voice Recognition</h3><p>Industry-leading voice recognition that works even in noisy environments.</p></div>
    <div class="abs feature" style="left:467px;top:731px"><span class="ico"></span><h3>Natural Speech</h3><p>Generates human-like responses with appropriate tone and context.</p></div>
    <div class="abs feature" style="left:65px;top:845px"><span class="ico"></span><h3>Lightning Fast</h3><p>Get responses in milliseconds, with no perceivable delay.</p></div>
    <div class="abs feature" style="left:266px;top:845px"><span class="ico"></span><h3>Private &amp; Secure</h3><p>Your conversations are encrypted and never stored without permission.</p></div>
    <div class="abs feature" style="left:467px;top:845px"><span class="ico"></span><h3>Multilingual Support</h3><p>Communicate in over 30 languages with accurate translations.</p></div>

    <h2 class="abs center sec-title hiw-title">How It Works</h2>
    <p class="abs center sec-sub hiw-sub">Simple, powerful, and intuitive</p>
    <div class="abs steps">
      <div class="step"><span class="step-num">1</span><div><h4>Speak Naturally</h4><p>Just talk to Vocalynx as you would to another person. No special commands needed.</p></div></div>
      <div class="step"><span class="step-num">2</span><div><h4>AI Processes</h4><p>Our advanced AI comprehends your words, understands context, and formulates a response.</p></div></div>
      <div class="step"><span class="step-num">3</span><div><h4>Get Instant Response</h4><p>Receive immediate, helpful replies that sound natural and address your needs.</p></div></div>
    </div>
    <div class="abs orbit" role="img" aria-label="Illustration of AI voice agent icons orbiting">
      <div class="orbit-ring"></div>
      <div class="orbit-node" style="left:20px;top:68px"></div>
      <div class="orbit-node" style="left:88px;top:26px"></div>
      <div class="orbit-node" style="left:100px;top:96px"></div>
    </div>

    <div class="abs pricing-bg"></div>
    <h2 class="abs center sec-title pricing-title">Pricing</h2>
    <p class="abs center sec-sub pricing-sub">Simple, transparent pricing for everyone</p>
    <div class="abs plan" style="left:73px">
      <div class="plan-tier">Basic</div><div class="plan-price">Free</div>
      <ul><li>100 voice interactions/month</li><li>Basic AI capabilities</li><li>Standard response time</li></ul>
      <div class="plan-btn">Get Started</div>
    </div>
    <div class="abs plan plan--popular" style="left:270px">
      <span class="plan-badge">Popular</span>
      <div class="plan-tier">Premium</div><div class="plan-price">$9.99 <small>/mo</small></div>
      <ul><li>Unlimited interactions</li><li>Advanced AI capabilities</li><li>Priority response time</li><li>Multi-language support</li></ul>
      <div class="plan-btn plan-btn--primary">Subscribe</div>
    </div>
    <div class="abs plan" style="left:467px">
      <div class="plan-tier">Enterprise</div><div class="plan-price">Custom</div>
      <ul><li>Dedicated instances</li><li>Custom AI training</li><li>API integrations</li><li>24/7 premium support</li></ul>
      <div class="plan-btn">Contact Sales</div>
    </div>

    <div class="abs footer-line"></div>
    <div class="abs footer-brand"><div class="brand"><span class="brand-dot"></span>VOCALYNX</div></div>
    <p class="abs footer-tag">The future of voice technology,<br>making AI accessible to everyone.</p>
    <div class="abs footer-col" style="left:454px"><h5>Product</h5><div>Features</div><div>Pricing</div><div>API</div><div>Integrations</div></div>
    <div class="abs footer-col" style="left:527px"><h5>Resources</h5><div>Documentation</div><div>Tutorials</div><div>Blog</div><div>Support</div></div>
    <div class="abs footer-col" style="left:610px"><h5>Company</h5><div>About</div><div>Careers</div><div>Privacy</div><div>Terms</div></div>
    <div class="abs footer-bottom"></div>
    <p class="abs copyright">© 2025 Vocalynx. All rights reserved.</p>
    <div class="abs social-dots"><span></span><span></span><span></span></div>
  </div>
</div>

</body>
</html>
```